Real Estate Company Looking for Business Card Designs for 3 Executives

Hello!
Thanks so much for considering our project! We are a real estate investment company located in Edmonton, Alberta called Bellhaven Group of Companies. We invest/develop both commercial and residential real estate and are looking to create 3 DOUBLE-SIDED business cards for 3 top executives in the company! (for some reason it won't let us select the double-sided option, but yes, the cards are double sided and would be happy to tip extra)

We have certain guidelines that we want our business cards to for sure follow - the back of the Business card has to be the Black Background Version of the Logo which has already been designed and linked as a file (first file). We want the entire back of the card to simply just be the black background logo. In terms of the front of the card, would like to see a smaller version of the white background logo (linked as the second file) in the top left hand corner - of course, feel free to get creative and we can make revisions together along the way! and Then after that, just text. We want the card to be sharp, clean, easy on the eyes and highly professional looking. We would like the card to include the Full name of the Company (Bellhaven Group of Companies), Name of the Person, Title, Phone, Email. If possible please provide the front part of the card for 3 people:

1) Bellhaven Group of Companies, Liora Quenby, Chief Financial Officer, 780-555-0142, lioraquenby@bellhavengroup.example

2) Bellhaven Group of Companies, Tobias Quenby, Chief Executive Officer, 780-555-0187, tobiasquenby@bellhavengroup.example

3) Bellhaven Group of Companies, Rui Delcourt, Chief Operations Officer, 587-555-0163, ruidelcourt@bellhavengroup.example

Thank you so much for considering our project & we look forward to seeing your designs!

```html
<!DOCTYPE html>
<html lang="en">
<head>
<meta charset="utf-8">
<title>Bellhaven Business Card</title>
<link rel="stylesheet" href="https://fonts.googleapis.com/css2?family=Roboto+Condensed:wght@300;400;700&display=swap">
<style>
  :root {
    --ink: #000000;
    --paper: #ffffff;
    --night: #050609;
    --stage: #eeeeee;
  }
  * { margin: 0; padding: 0; box-sizing: border-box; }
  html, body { width: 1200px; height: 848px; overflow: hidden; }
  body {
    background: var(--stage);
    position: relative;
    font-family: "Roboto Condensed", sans-serif;
    color: var(--ink);
  }
  .card {
    position: absolute;
    left: 331px;
    width: 538px;
    height: 309px;
    box-shadow: 8px 10px 14px rgba(0,0,0,0.18);
  }
  .card-front {
    top: 90px;
    background: var(--paper);
    border: 1px solid var(--ink);
    overflow: hidden;
  }
  .card-back {
    top: 449px;
    background: var(--night);
  }
  .brand {
    position: absolute;
    display: flex;
    align-items: center;
    font-weight: 700;
    letter-spacing: 0.12em;
    line-height: 1;
  }
  .brand-mark { display: block; flex: none; }
  .card-front .brand {
    left: 65px; top: 58px;
    font-size: 30px;
    color: var(--ink);
    gap: 10px;
  }
  .card-front .brand-mark { width: 26px; height: 26px; background: var(--ink); }
  .card-back .brand {
    left: 0; right: 0; top: 132px;
    justify-content: center;
    font-size: 46px;
    color: var(--paper);
    gap: 14px;
  }
  .card-back .brand-mark { width: 38px; height: 38px; background: var(--paper); }
  .person {
    position: absolute;
    left: 65px; top: 176px;
  }
  .person-name { font-size: 21px; font-weight: 700; line-height: 1.1; }
  .person-title { font-size: 12.5px; font-weight: 400; margin-top: 9px; }
  .divider {
    position: absolute;
    left: 204px; top: 186px;
    width: 1px; height: 40px;
    background: var(--ink);
  }
  .contact {
    position: absolute;
    left: 239px; top: 181px;
    list-style: none;
    font-size: 16.5px;
    font-weight: 300;
  }
  .contact li { display: flex; align-items: center; height: 24px; }
  .contact svg { width: 18px; height: 16px; margin-right: 8px; flex: none; }
  .rule {
    position: absolute; left: 0; right: 0;
    height: 1.5px; background: var(--ink);
  }
  .rule-1 { top: 259px; }
  .rule-2 { top: 264px; }
  .rule-3 { top: 269px; }
  .company-band {
    position: absolute; left: 0; right: 0; bottom: 0;
    height: 37px;
    background: var(--ink);
    color: var(--paper);
    display: flex; align-items: center; justify-content: center;
    font-size: 13px;
    letter-spacing: 0.32em;
    font-weight: 400;
  }
</style>
</head>
<body>
  <section class="card card-front">
    <div class="brand"><span class="brand-mark"></span>BELLHAVEN</div>

    <div class="person">
      <p class="person-name">Liora Quenby</p>
      <p class="person-title">Chief Financial Officer</p>
    </div>
    <div class="divider"></div>
    <ul class="contact">
      <li>
        <svg viewBox="0 0 24 24" aria-hidden="true"><path fill="currentColor" d="M6.6 2.5c.6-.4 1.4-.2 1.8.4l2.2 3.6c.4.6.2 1.3-.3 1.7L9 9.1c.9 2.4 2.6 4.6 4.9 6l1.2-1.2c.5-.5 1.3-.5 1.8-.1l3.2 2.6c.6.5.7 1.3.2 1.9l-1.5 1.9c-.7.9-2 1.2-3 .7C9.6 18.2 5.4 12.6 4.5 6.2c-.1-.9.3-1.8 1-2.3z"/></svg>
        780-555-0142
      </li>
      <li>
        <svg viewBox="0 0 24 18" aria-hidden="true"><path fill="currentColor" d="M1 1h22v16H1zM3 3v.4l9 6.3 9-6.3V3zm0 2.8V15l6-4.6zm18 0-6 4.6 6 4.6zM10.8 11.5 4.4 15h15.2l-6.4-3.5-1.2.9z"/></svg>
        lioraquenby@bellhavengroup.example
      </li>
    </ul>

    <div class="rule rule-1"></div>
    <div class="rule rule-2"></div>
    <div class="rule rule-3"></div>
    <div class="company-band">BELLHAVEN GROUP OF COMPANIES</div>
  </section>

  <section class="card card-back">
    <div class="brand"><span class="brand-mark"></span>BELLHAVEN</div>
  </section>
</body>
</html>
```